Tessmar Fahrwerkstatt
Sehr angenehme zusammenarbeit nicht aufdringlich und genau auf die Wünsche eingegangen. Wir werde sicher noch mehr zusammen Arbeiten. Gruss Lukas Hegemann Inhaber Tessmar Fahrwerkstatt
Zielgruppe
Dinks und Kunden mit viel Erfolg und hohem Ausgabepotential.
Aufgabenstellung
Unsere Firma vertreibt Fahrzeuge im Luxusbereich hauptgebiet Valmerra aber auch andere Sportwagen. Was uns fehlt ist ein optischer Wiedererkennugswert. Deshalb hätten wir gerne ein Visitenkarten Design und Briefpapier Design. Später soll auch noch eine Webseite mit gleichem Wiedererkennungswert entstehen. " Roter Faden "

```html
<!DOCTYPE html>
<html lang="de">
<head>
<meta charset="utf-8">
<title>Tessmar Fahrwerkstatt – Visitenkarte</title>
<link rel="stylesheet" href="https://fonts.googleapis.com/css2?family=Inter:wght@200;300;700&display=swap">
<style>
  :root {
    --stage: #e4e4e4;
    --card-white: #ffffff;
    --card-black: #000000;
    --ink-light: #ffffff;
    --ink-muted: #d6d6d6;
    --ink-dark: #111111;
  }
  * { box-sizing: border-box; margin: 0; padding: 0; }
  html, body {
    width: 1200px; height: 800px; overflow: hidden;
    background: var(--stage);
    font-family: "Inter", "Helvetica Neue", Arial, sans-serif;
  }
  .business-card {
    position: absolute; left: 100px; top: 100px;
    width: 1000px; height: 600px;
    background: var(--card-white);
    overflow: hidden;
    box-shadow: 0 14px 40px rgba(0,0,0,0.18);
  }
  .black-sweep { position: absolute; inset: 0; }
  .contact-block {
    position: absolute; right: 530px; top: 215px;
    text-align: right; color: var(--ink-muted);
    font-weight: 300; white-space: nowrap;
  }
  .holder-name {
    color: var(--ink-light); font-weight: 200;
    font-size: 34px; letter-spacing: 3px; margin-bottom: 12px;
  }
  .location-label {
    font-size: 10px; font-weight: 700; color: var(--ink-light);
    letter-spacing: 0.5px; margin-bottom: 8px;
  }
  .location-address { font-size: 19px; margin-bottom: 44px; }
  .contact-lines { font-size: 17px; line-height: 30px; margin-top: -6px; }
  .brand-mark {
    position: absolute; left: 560px; top: 50px; color: var(--ink-dark);
  }
  .brand-dot {
    width: 66px; height: 66px; border-radius: 50%;
    background: var(--card-black); margin-left: 2px; margin-bottom: 10px;
  }
  .brand-name {
    font-weight: 200; font-size: 62px; line-height: 62px; letter-spacing: 3px;
  }
  .brand-sub {
    font-weight: 200; font-size: 26px; letter-spacing: 4px; margin-top: 6px;
  }
</style>
</head>
<body>
  <div class="business-card">
    <svg class="black-sweep" width="1000" height="600" viewBox="0 0 1000 600" aria-hidden="true">
      <path d="M0 0 H318 C470 120 575 340 540 600 H0 Z" fill="var(--card-black)"/>
    </svg>

    <div class="contact-block">
      <p class="holder-name">LUKAS HEGEMANN</p>
      <p class="location-label">BÜRO</p>
      <p class="location-address">Lindenweg 12 - CH 8153 Rümlang</p>
      <p class="location-label">SHOWROOM</p>
      <p class="location-address">Mühlegasse 9 - CH 8604 Hegnau</p>
      <div class="contact-lines">
        <p>+41795180274</p>
        <p>info@tessmar.ch</p>
        <p>www.tessmar.ch</p>
      </div>
    </div>

    <div class="brand-mark">
      <div class="brand-dot"></div>
      <p class="brand-name">TESSMAR</p>
      <p class="brand-sub">FAHRWERKSTATT</p>
    </div>
  </div>
</body>
</html>
```